Stonebridge Building and Projects business cards

A business card with watermark background (construction work)

Company logo attached

Home improvement projects
House renovations
Bathroom and kitchen renovations
House extensions
New builds and granny flats

Director Omar Haddani
(Phone number)
omar@sbpbuilding.com.au
(Instagram logo) sbp_building

```html
<!DOCTYPE html>
<html lang="en">
<head>
<meta charset="utf-8">
<title>Stonebridge Building and Projects – Business Cards</title>
<link rel="stylesheet" href="https://fonts.googleapis.com/css2?family=Roboto:wght@400;500;700&family=Roboto+Slab:wght@500&display=swap">
<style>
  :root {
    --stage: #2b2b2d;
    --card: #f4f5f6;
    --brand-blue: #1273bd;
    --ink: #3d3f44;
    --edge-grey: #3a3f46;
    --white: #ffffff;
  }
  * { margin: 0; padding: 0; box-sizing: border-box; }
  html, body { width: 1200px; height: 1050px; overflow: hidden; }
  body {
    background: var(--stage);
    font-family: "Roboto", Arial, sans-serif;
    position: relative;
  }
  .card {
    position: absolute;
    left: 250px;
    width: 700px;
    height: 400px;
    border-radius: 28px;
    background: var(--card);
    overflow: hidden;
  }
  .card--front { top: 90px; }
  .card--back { top: 560px; }

  .site-watermark {
    position: absolute;
    inset: 0;
    background: radial-gradient(ellipse at 40% 60%, rgba(190,194,200,0.35), rgba(244,245,246,0) 70%);
  }

  /* brand block */
  .brand { position: absolute; text-align: center; }
  .brand__name {
    font-weight: 700;
    font-size: 34px;
    line-height: 1.1;
    color: var(--brand-blue);
  }
  .brand__mark {
    display: inline-block;
    width: 26px; height: 26px;
    background: var(--brand-blue);
    margin-bottom: 10px;
  }
  .brand__tagline {
    font-family: "Roboto Slab", Georgia, serif;
    font-weight: 500;
    font-size: 22px;
    color: var(--brand-blue);
    margin-top: 8px;
    padding: 2px 10px;
    border-top: 2px solid var(--brand-blue);
    border-bottom: 2px solid var(--brand-blue);
    display: inline-block;
  }
  .card--front .brand { left: 0; right: 0; top: 36px; }

  .services-band {
    position: absolute;
    left: 0; right: 0; top: 248px;
    height: 74px;
    background: var(--brand-blue);
    color: var(--white);
    font-size: 18px;
    line-height: 26px;
    text-align: center;
    padding-top: 11px;
  }
  .social-row {
    position: absolute;
    left: 0; right: 0; top: 340px;
    display: flex;
    justify-content: center;
    gap: 40px;
    font-size: 17px;
    color: var(--ink);
  }
  .social-row span, .contact-list li {
    display: flex; align-items: center; gap: 10px;
  }
  .icon { width: 20px; height: 20px; flex: none; }

  /* back */
  .back-panel { position: absolute; inset: 0; }
  .card--back .brand {
    left: 400px; width: 290px; top: 72px;
  }
  .card--back .brand__name { color: var(--white); font-size: 28px; }
  .card--back .brand__mark { background: var(--white); width: 22px; height: 22px; }
  .card--back .brand__tagline {
    color: var(--white); border-color: var(--white); font-size: 19px;
  }
  .person { position: absolute; left: 70px; top: 212px; }
  .person__name {
    font-size: 27px; font-weight: 700; color: var(--brand-blue);
  }
  .person__role { font-size: 17px; color: var(--ink); margin-top: 2px; }
  .contact-list {
    list-style: none;
    margin-top: 18px;
    font-size: 17px;
    color: var(--ink);
  }
  .contact-list li { margin-bottom: 7px; }
</style>
</head>
<body>

<section class="card card--front">
  <div class="site-watermark" role="img" aria-label="Faint construction work photograph as background watermark"></div>
  <div class="brand">
    <div class="brand__mark"></div>
    <div class="brand__name">Stonebridge Building<br>and Projects</div>
    <div class="brand__tagline">Built right, first time!</div>
  </div>
  <div class="services-band">
    Home Improvement Projects &nbsp;|&nbsp; House Renovations &nbsp;|&nbsp; House Extensions<br>
    Bathroom &amp; Kitchen Renovations &nbsp;|&nbsp; New Builds &amp; Granny Flats
  </div>
  <div class="social-row">
    <span>
      <svg class="icon" viewBox="0 0 20 20"><circle cx="10" cy="10" r="9" fill="var(--brand-blue)"/></svg>
      sbp_building
    </span>
    <span>
      <svg class="icon" viewBox="0 0 20 20" fill="none" stroke="var(--brand-blue)" stroke-width="1.6"><circle cx="10" cy="10" r="8.5"/><ellipse cx="10" cy="10" rx="3.8" ry="8.5"/><path d="M1.5 10h17M3 5.5h14M3 14.5h14"/></svg>
      sbpbuilding.com.au
    </span>
  </div>
</section>

<section class="card card--back">
  <div class="site-watermark" role="img" aria-label="Faint construction work photograph as background watermark"></div>
  <svg class="back-panel" viewBox="0 0 700 400" preserveAspectRatio="none">
    <path d="M398 0 C 305 150, 345 330, 460 400 L 700 400 L 700 0 Z" fill="var(--edge-grey)"/>
    <path d="M420 0 C 335 150, 380 320, 490 400 L 700 400 L 700 0 Z" fill="var(--brand-blue)"/>
  </svg>
  <div class="brand">
    <div class="brand__mark"></div>
    <div class="brand__name">Stonebridge Building<br>and Projects</div>
    <div class="brand__tagline">Built right, first time!</div>
  </div>
  <div class="person">
    <div class="person__name">Omar Haddani</div>
    <div class="person__role">Managing Director</div>
    <ul class="contact-list">
      <li>
        <svg class="icon" viewBox="0 0 20 20"><circle cx="10" cy="10" r="8.5" fill="none" stroke="var(--brand-blue)" stroke-width="1.5"/><path d="M7 5.5l2 2-1 1.3c.6 1.3 1.5 2.2 2.8 2.8l1.3-1 2 2-1.3 1.6C9.8 14 6 10.2 5.6 6.8z" fill="var(--brand-blue)"/></svg>
        0400 317 862
      </li>
      <li>
        <svg class="icon" viewBox="0 0 20 20" fill="none" stroke="var(--brand-blue)" stroke-width="1.6"><rect x="2" y="4.5" width="16" height="11" rx="1"/><path d="M2.5 5l7.5 6 7.5-6"/></svg>
        omar@sbpbuilding.com.au
      </li>
      <li>
        <svg class="icon" viewBox="0 0 20 20" fill="none" stroke="var(--brand-blue)" stroke-width="1.6"><circle cx="10" cy="10" r="8.5"/><ellipse cx="10" cy="10" rx="3.8" ry="8.5"/><path d="M1.5 10h17"/></svg>
        sbpbuilding.com.au
      </li>
      <li>
        <svg class="icon" viewBox="0 0 20 20"><circle cx="10" cy="10" r="9" fill="var(--brand-blue)"/></svg>
        sbp_building
      </li>
    </ul>
  </div>
</section>

</body>
</html>
```